Low Ferry Guild - Wavering CD Cover

To prepare a CD Cover for the single "Wavering" by Low Ferry Guild.
You can hear the single here:
http://lowferryguild-band.example/listen/

The LFG logo and backdrop are also provided if you want to incorporate them into the CD cover design, though that isn't mandatory.

Song is about deciding on taking on a serious relationship, and leaving the single life behind.

Target Market(s)

Music listeners, 18-50 yrs old, into retro 80s, Marrowmen/Tide Rollers

Industry/Entity Type

Music Download

Requirements
Must have
• LFG logo
• Wavering title
Nice to have
• Use of backdrop, or facimile
Should not have
• Too obvious on the term Wavering

```html
<!DOCTYPE html>
<html lang="en">
<head>
<meta charset="utf-8">
<title>Low Ferry Guild – Wavering</title>
<link rel="stylesheet" href="https://fonts.googleapis.com/css2?family=Big+Shoulders+Display:wght@600&family=Josefin+Sans:wght@200&display=swap">
<style>
  :root {
    --paper: #ffffff;
    --ink-logo: #25164a;
    --ink-title: #111111;
  }
  html, body {
    margin: 0;
    padding: 0;
    overflow: hidden;
    background: var(--paper);
  }
  .cover {
    position: relative;
    width: 1200px;
    height: 1200px;
    background: var(--paper);
    overflow: hidden;
  }
  .band-name {
    position: absolute;
    left: 0;
    top: 0;
    width: 1200px;
    height: 1000px;
  }
  .band-name text {
    font-family: "Big Shoulders Display", "Arial Narrow", sans-serif;
    font-weight: 600;
    fill: var(--ink-logo);
  }
  .single-title {
    position: absolute;
    left: 152px;
    top: 1036px;
    width: 932px;
    margin: 0;
    display: flex;
    justify-content: space-between;
    font-family: "Josefin Sans", sans-serif;
    font-weight: 200;
    font-size: 50px;
    line-height: 1;
    color: var(--ink-title);
  }
</style>
</head>
<body>
  <main class="cover">
    <svg class="band-name" viewBox="0 0 1200 1000" role="img" aria-label="Low Ferry Guild">
      <text x="360" y="432" font-size="380" textLength="486" lengthAdjust="spacingAndGlyphs">LOW</text>
      <text x="360" y="724" font-size="345" textLength="488" lengthAdjust="spacingAndGlyphs">FERRY</text>
      <text x="356" y="936" font-size="234" textLength="502" lengthAdjust="spacingAndGlyphs">GUILD</text>
    </svg>
    <h1 class="single-title" aria-label="Wavering">
      <span>W</span><span>A</span><span>V</span><span>E</span><span>R</span><span>I</span><span>N</span><span>G</span>
    </h1>
  </main>
</body>
</html>
```